Local massage therapist needs some new marketing material

Hi there! I am a massage therapist here in Denver, CO in Alder Bend(shopping and art district) of the city. My business is called Lumo Bodywork of Denver. My practice has an eastern influence and I do reflexology, thai massage and use Chinese herbs, etc. I know all my clients and pay close attention to details. I am also very respectful of tradition and it shows in how I work. I tend to like modern, clean, fun, Asian designs. I am wanting a new business card and brochure. I have a logo and branding for my business that I want used in the design. Currently, the sign for my building is purple and I think my logo was designed to be purple. I will attach pictures of it and can send whatever files are necessary so it can be integrated into the brochure, etc. I like the purple but open to using other colors as well. Thanks!
My website is lumobodyworkofdenver.example where info can be gathered about me and services/fees for brochure.
Updates

Just increased budget. Please see new feedback in discussion thread.

Thanks!

                                       HEY ALL,

Just wanted to let you know that I made a change to my website. It is on the Prices Page. I no longer have the frequent  flyer prices but I added discounts. Let me know if you have any questions. Thanks so much!

Target Market(s)

healthy, urban, educated, upper middle class, yogis

Industry/Entity Type

Marketing

Requirements
Must have
• logo stays purple
Should not have
• not too busy

```html
<!DOCTYPE html>
<html lang="en">
<head>
<meta charset="utf-8">
<title>Lumo Bodywork of Denver – Business Card</title>
<link href="https://fonts.googleapis.com/css2?family=Open+Sans:ital,wght@0,400;0,600;0,700;1,400&display=swap" rel="stylesheet">
<style>
  :root {
    --purple: #6a2d9b;
    --purple-deep: #5b2389;
    --ink: #3d3d3d;
    --muted: #6f6f6f;
    --rule: #2e2e2e;
    --paper: #ffffff;
    --stage: #ecebee;
  }
  * { box-sizing: border-box; margin: 0; padding: 0; }
  html, body {
    width: 1200px; height: 720px; overflow: hidden;
    background: var(--stage);
    font-family: "Open Sans", Arial, sans-serif;
    color: var(--ink);
  }
  .sheet {
    position: relative; width: 1200px; height: 720px;
    display: flex; align-items: center; justify-content: center; gap: 40px;
  }
  .card {
    position: relative; width: 540px; height: 309px;
    background: var(--paper);
    box-shadow: 0 2px 10px rgba(0,0,0,.12);
    overflow: hidden;
  }

  /* Front */
  .brand {
    position: absolute; left: 0; right: 0; top: 52px;
    display: flex; align-items: center; justify-content: center; gap: 14px;
    padding-right: 70px;
  }
  .brand-dot { width: 18px; height: 18px; border-radius: 50%; background: var(--purple); }
  .brand-name {
    font-weight: 600; font-size: 56px; letter-spacing: 10px;
    color: var(--purple); line-height: 1;
  }
  .front-rule {
    position: absolute; left: 0; right: 0; top: 164px; height: 3px; background: var(--rule);
  }
  .contact-band {
    position: absolute; left: 0; right: 0; top: 172px; bottom: 0;
    background: var(--purple);
    color: #fff;
    display: flex; align-items: center;
  }
  .person {
    width: 47%; text-align: right; padding-right: 18px;
    font-size: 14px; line-height: 1.35;
  }
  .person-name { font-weight: 700; font-size: 18px; }
  .person-title { font-size: 13px; margin-bottom: 6px; }
  .band-divider { width: 1px; align-self: stretch; margin: 18px 0; background: rgba(255,255,255,.75); }
  .contact-list { list-style: none; padding-left: 16px; font-size: 13.5px; line-height: 1.9; }
  .contact-list li { display: flex; align-items: center; gap: 7px; }
  .contact-list svg { width: 14px; height: 14px; flex: none; }

  /* Back */
  .appointment {
    position: absolute; inset: 0; padding: 56px 40px 0;
    text-align: center;
  }
  .appt-heading {
    color: var(--purple); font-weight: 700; font-size: 15px; letter-spacing: .3px;
    margin-bottom: 22px;
  }
  .appt-row {
    display: flex; align-items: flex-end; gap: 8px;
    font-size: 15px; margin-bottom: 18px; text-align: left;
  }
  .appt-line { flex: 1; border-bottom: 1px dotted var(--muted); height: 16px; }
  .appt-line.short { flex: .8; }
  .hours { font-size: 15px; line-height: 1.45; margin-top: 8px; }
  .cancel-note { font-style: italic; color: var(--muted); font-size: 14.5px; margin-top: 22px; }
</style>
</head>
<body>
<main class="sheet">

  <section class="card card-front" aria-label="Business card front">
    <div class="brand">
      <span class="brand-dot"></span>
      <span class="brand-name">LUMO</span>
    </div>
    <div class="front-rule"></div>
    <div class="contact-band">
      <div class="person">
        <div class="person-name">Your Name</div>
        <div class="person-title">Title</div>
        <div>1450 E 4th Ave, Denver</div>
        <div>CO 80218</div>
      </div>
      <div class="band-divider"></div>
      <ul class="contact-list">
        <li>
          <svg viewBox="0 0 16 16" aria-hidden="true"><circle cx="8" cy="8" r="8" fill="#fff"/><path d="M5.2 4.2l1.4-.4.9 2-1 .8c.5 1.1 1.3 1.9 2.4 2.4l.8-1 2 .9-.4 1.4c-3.2.3-6.4-2.9-6.1-6.1z" fill="#6a2d9b"/></svg>
          303.555.0187
        </li>
        <li>
          <svg viewBox="0 0 16 16" aria-hidden="true"><circle cx="8" cy="8" r="8" fill="#fff"/><rect x="4" y="5" width="8" height="6" rx=".6" fill="#6a2d9b"/><path d="M4.2 5.4L8 8.4l3.8-3" stroke="#fff" stroke-width=".9" fill="none"/></svg>
          info@lumobodyworkofdenver.example
        </li>
        <li>
          <svg viewBox="0 0 16 16" aria-hidden="true"><circle cx="8" cy="8" r="8" fill="#fff"/><g stroke="#6a2d9b" stroke-width=".9" fill="none"><circle cx="8" cy="8" r="4.2"/><ellipse cx="8" cy="8" rx="1.8" ry="4.2"/><path d="M3.8 8h8.4"/></g></svg>
          www.lumobodyworkofdenver.example
        </li>
      </ul>
    </div>
  </section>

  <section class="card card-back" aria-label="Business card back">
    <div class="appointment">
      <h2 class="appt-heading">YOUR APPOINTMENT</h2>
      <div class="appt-row">
        <span>Name :</span><span class="appt-line"></span>
        <span>Time :</span><span class="appt-line short"></span><span>am / pm</span>
      </div>
      <div class="appt-row">
        <span>Date :</span><span class="appt-line"></span>
      </div>
      <p class="hours">Tues - Fri 10am - 8pm Sat 10am-5pm<br>(Appointments required) No walk-ins please.</p>
      <p class="cancel-note">We appreciate a 24 hr. notice for cancellations</p>
    </div>
  </section>

</main>
</body>
</html>
```